Building company buisness cards

We are looking for a sharp modern new look for our business cards.We are a New Zealand based company that specialises in house and land packages.We have attached a photo of the current logo and would like to see if it can be improved somehow if needed.We are open to any colours but we have chosen Black and White at this stage. Feel free to change the font and make the logo smarter looking.Play with the colours and see what looks best.We want a card that looks so good know one will want to throw it away!

Target Market(s)

Building profesonals, home buyers

Industry/Entity Type

Building

Contact Information for Business Card

Garrick Tenwood
0275390628
garrickt@hartvale.co.nz

Font styles to use
Serif
Sans Serif

Colors

Designer to choose colors to be used in the design.

Requirements
Must have
• Just the logo on one side and details on the other
• Clean simple looking card
Nice to have
• Round corners and detail like raised or spot UV
• Something that stands out
Should not have
• To title needed, Director etc

```html
<!DOCTYPE html>
<html lang="en">
<head>
<meta charset="utf-8">
<title>Hartvale Business Card</title>
<link href="https://fonts.googleapis.com/css2?family=Work+Sans:wght@400;500;600&display=swap" rel="stylesheet">
<style>
  :root {
    --backdrop: #1c1c1d;
    --card: #141414;
    --card-edge: #202021;
    --ink: #f4f4f4;
    --ink-soft: #dcdcdc;
  }
  * { margin: 0; padding: 0; box-sizing: border-box; }
  html, body {
    width: 1200px; height: 900px; overflow: hidden;
    background: var(--backdrop);
    font-family: "Work Sans", Arial, sans-serif;
    color: var(--ink);
  }
  .sheet {
    width: 1200px; height: 900px;
    display: flex; flex-direction: column; align-items: center; justify-content: center;
    gap: 40px;
  }
  .card {
    width: 660px; height: 380px;
    background: linear-gradient(135deg, var(--card) 0%, var(--card-edge) 100%);
    border-radius: 14px;
    box-shadow: 0 18px 40px rgba(0,0,0,0.55);
    position: relative;
  }
  .card--front { display: flex; align-items: center; justify-content: center; }
  .brand { display: flex; align-items: center; gap: 16px; }
  .brand__name {
    font-weight: 600; font-size: 58px; letter-spacing: -1px; line-height: 1;
    color: var(--ink);
  }
  .brand__circle {
    width: 64px; height: 64px; border: 3px solid var(--ink); border-radius: 50%;
  }
  .card--back { display: flex; align-items: center; padding: 0 50px; }
  .card--back .brand__name { font-size: 46px; }
  .card--back .brand__circle { width: 52px; height: 52px; }
  .divider {
    width: 2px; height: 200px; background: var(--ink); margin: 0 36px 0 34px;
  }
  .details { display: flex; flex-direction: column; }
  .details__name {
    font-size: 21px; font-weight: 500; letter-spacing: 1.5px; text-transform: uppercase;
  }
  .details__role { font-size: 15px; color: var(--ink-soft); margin-top: 2px; }
  .details__address { font-size: 16px; line-height: 1.4; margin-top: 16px; color: var(--ink-soft); }
  .contact { list-style: none; margin-top: 12px; font-size: 16px; color: var(--ink-soft); }
  .contact__item { display: flex; align-items: center; gap: 10px; line-height: 1.6; }
  .contact__icon { width: 12px; height: 12px; flex: none; }
</style>
</head>
<body>
<main class="sheet">
  <section class="card card--front" aria-label="Card front">
    <div class="brand">
      <span class="brand__name">Hartvale</span>
      <span class="brand__circle" aria-hidden="true"></span>
    </div>
  </section>

  <section class="card card--back" aria-label="Card back">
    <div class="brand">
      <span class="brand__name">Hartvale</span>
      <span class="brand__circle" aria-hidden="true"></span>
    </div>
    <div class="divider" aria-hidden="true"></div>
    <div class="details">
      <p class="details__name">Garrick Tenwood</p>
      <p class="details__role">Director</p>
      <p class="details__address">218b Marlow Road,<br>Kaiapoi, NZ, 7630</p>
      <ul class="contact">
        <li class="contact__item">
          <svg class="contact__icon" viewBox="0 0 12 12" fill="none" stroke="#f4f4f4" stroke-width="1.2"><path d="M2.5 1h2l1 2.5-1.3 1a6 6 0 0 0 3.3 3.3l1-1.3L11 7.5v2a1.5 1.5 0 0 1-1.5 1.5A8.5 8.5 0 0 1 1 2.5 1.5 1.5 0 0 1 2.5 1z"/></svg>
          <span>0275390628</span>
        </li>
        <li class="contact__item">
          <svg class="contact__icon" viewBox="0 0 12 12" fill="none" stroke="#f4f4f4" stroke-width="1.2"><rect x="1" y="2.5" width="10" height="7" rx="0.5"/><path d="M1 3l5 3.5L11 3"/></svg>
          <span>garrickt@hartvale.co.nz</span>
        </li>
        <li class="contact__item">
          <svg class="contact__icon" viewBox="0 0 12 12" fill="none" stroke="#f4f4f4" stroke-width="1"><circle cx="6" cy="6" r="5"/><ellipse cx="6" cy="6" rx="2.2" ry="5"/><path d="M1 6h10M2 3.3h8M2 8.7h8"/></svg>
          <span>www.hartvale.co.nz</span>
        </li>
      </ul>
    </div>
  </section>
</main>
</body>
</html>
```